Modern Business Card for Larkwell 2018

Our company assumes the best about people. We are creating an online community of entrepreneurs and business leaders who struggle with marketing their business online.

This business card should POP! We recently got a new logo and are launching a new website next month, so our business cards should make a statement that feels:
-Fresh
-Smart
-Trustworthy
-Fun

Target Market(s)

small business owners, entrepreneurs

Industry/Entity Type

Digital Marketing

Contact Information for Business Card

Dimensions: 3.5" x 2"

Font styles to use
Sans Serif

Colors
f37122
ffffff

Requirements
Must have
• We need a business card with a modern, bold design. We will use one side of the card as a lead-generation offer, so text on one side will need to fit up to 140 characters. The business card should stick to our core colors (orange, black, and white).
Nice to have
• We think a vertical "portrait" design could be interesting.
Should not have
• Should not look like a traditional business card. The round icon should stand out from a distance.

```html
<!DOCTYPE html>
<html lang="en">
<head>
<meta charset="utf-8">
<title>Larkwell Business Card</title>
<link rel="stylesheet" href="https://fonts.googleapis.com/css2?family=Open+Sans:wght@400;600;700;800&display=swap">
<style>
  :root {
    --orange: #f37122;
    --white: #ffffff;
    --ink: #1a1a1a;
    --stage: #3a3a3a;
    --field: #e9e9e9;
    --field-line: #6e6e6e;
    --divider: rgba(255, 255, 255, 0.45);
  }
  * { box-sizing: border-box; margin: 0; padding: 0; }
  html, body {
    width: 1200px;
    height: 960px;
    overflow: hidden;
  }
  body {
    background: var(--stage);
    font-family: "Open Sans", Arial, sans-serif;
    display: flex;
    flex-direction: column;
    align-items: center;
    justify-content: center;
    gap: 60px;
  }
  .card {
    position: relative;
    width: 700px;
    height: 400px;
    border-radius: 6px;
    overflow: hidden;
    box-shadow: 0 10px 30px rgba(0, 0, 0, 0.35);
  }

  /* Back: lead-generation side */
  .card-back { background: var(--orange); color: var(--white); }
  .back-mark {
    position: absolute;
    left: 78px;
    top: 56px;
    width: 176px;
    height: 176px;
    border-radius: 50%;
    background: var(--white);
  }
  .back-divider {
    position: absolute;
    left: 318px;
    top: 40px;
    width: 1px;
    height: 180px;
    background: var(--divider);
  }
  .offer {
    position: absolute;
    left: 350px;
    top: 40px;
    right: 30px;
  }
  .offer-headline {
    font-weight: 800;
    font-size: 22px;
    line-height: 1.05;
    text-transform: uppercase;
    letter-spacing: 0.2px;
  }
  .offer-body {
    margin-top: 8px;
    font-size: 15px;
    line-height: 1.3;
    font-weight: 400;
  }
  .offer-url {
    margin-top: 10px;
    font-weight: 700;
    font-size: 17px;
  }
  .write-in {
    position: absolute;
    left: 70px;
    right: 36px;
    top: 250px;
    height: 110px;
    border-radius: 18px;
    background: var(--field);
    padding: 32px 36px 0 60px;
  }
  .write-in .rule {
    height: 1px;
    background: var(--field-line);
    margin-bottom: 30px;
  }

  /* Front: contact side */
  .card-front { background: var(--white); color: var(--ink); }
  .brand {
    position: absolute;
    left: 330px;
    top: 110px;
    width: 320px;
    text-align: center;
  }
  .brand-dot {
    display: block;
    width: 34px;
    height: 34px;
    margin: 0 auto 6px;
    border-radius: 50%;
    background: var(--orange);
  }
  .brand-name {
    font-weight: 800;
    font-size: 50px;
    letter-spacing: 2px;
    line-height: 1;
  }
  .brand-tagline {
    margin-top: 6px;
    font-weight: 700;
    font-size: 12.5px;
    letter-spacing: 1.4px;
    text-transform: uppercase;
  }
  .contact-band {
    position: absolute;
    left: 0;
    bottom: 0;
    width: 360px;
    height: 160px;
    background: var(--orange);
    clip-path: polygon(0 0, 86% 0, 100% 100%, 0 100%);
    color: var(--white);
    padding: 34px 0 0 38px;
  }
  .contact-name {
    font-weight: 800;
    font-size: 22px;
    text-transform: uppercase;
    line-height: 1.1;
  }
  .contact-role {
    font-weight: 700;
    font-size: 17px;
    text-transform: uppercase;
    line-height: 1.3;
  }
  .contact-email {
    font-size: 15px;
    font-weight: 400;
  }
</style>
</head>
<body>

  <section class="card card-back" aria-label="Card back: lead offer">
    <span class="back-mark" aria-hidden="true"></span>
    <span class="back-divider" aria-hidden="true"></span>
    <div class="offer">
      <p class="offer-headline">Find new customers.<br>Grow your revenue.<br>Build lasting trust.</p>
      <p class="offer-body">Get your free Larkwell<br>Starter Package and our<br>marketing guide today at</p>
      <p class="offer-url">Larkwellnow.com/start</p>
    </div>
    <div class="write-in" aria-label="Write-in field">
      <div class="rule"></div>
      <div class="rule"></div>
    </div>
  </section>

  <section class="card card-front" aria-label="Card front: contact">
    <div class="brand">
      <span class="brand-dot" aria-hidden="true"></span>
      <p class="brand-name">LARKWELL</p>
      <p class="brand-tagline">Craft messages that spark growth</p>
    </div>
    <div class="contact-band">
      <p class="contact-name">Dana Whitfield</p>
      <p class="contact-role">Story Marketing Coach</p>
      <p class="contact-email">dana@larkwellnow.com</p>
    </div>
  </section>

</body>
</html>
```